Auntie Verdict Billboard

I need a billboard designed for a Personal Injury Law firm. I need to simple not busy. I am attaching the following as suggestions to use. Need good colors that show up from Road Simple that can leave people associating injury lawyer with Auntie Verdict. Big picture of Dottie. Need Auntieverdict.com and 555-417-9038 to be big. possiblly let the emojis do the talking for personal injury and money settlement. Colors for logo should be similar to website auntieverdict.com
Updates

Billboard size. 10.5ft. X 36ft.

Target Market(s)

Car Accident Victims

Font styles to use
Sans Serif

Requirements
Must have
• Picture of Dottie. auntieverdict.com. 555-417-9038. message needs to be clear that she is a personal injury attorney. Clear simple message. Colors bold and visable to highway drivers
Should not have
• Busy ad.

```html
<!DOCTYPE html>
<html lang="en">
<head>
<meta charset="utf-8">
<title>Auntie Verdict Billboard</title>
<link rel="stylesheet" href="https://fonts.googleapis.com/css2?family=Lato:wght@400;700;900&display=swap">
<style>
  :root {
    --red: #c01f32;
    --navy: #0f1f6b;
    --white: #ffffff;
    --stage: #6a6a6a;
    --cash-light: #a6d44a;
    --cash-dark: #5e8f22;
    --suit: #141414;
    --hair: #2a1d1a;
  }
  * { margin: 0; padding: 0; box-sizing: border-box; }
  html, body {
    width: 1200px; height: 960px; overflow: hidden;
    background: var(--stage);
    font-family: "Lato", sans-serif;
  }
  .billboard {
    position: absolute; left: 40px; top: 316px;
    width: 1120px; height: 327px;
    background: var(--white);
    overflow: hidden;
    box-shadow: 0 18px 30px rgba(0,0,0,.35);
  }
  .emoji-art {
    position: absolute; left: 125px; top: 31px;
    width: 209px; height: 133px;
    border-radius: 24px;
    background: radial-gradient(ellipse at 50% 50%, var(--cash-light) 0%, var(--cash-dark) 75%, rgba(255,255,255,0) 100%);
  }
  .firm {
    position: absolute; left: 62px; top: 184px;
    width: 310px;
  }
  .firm-name {
    display: flex; align-items: flex-end; gap: 8px;
    color: var(--navy);
    font-weight: 700; font-size: 24px; line-height: 30px;
    letter-spacing: 1px; white-space: nowrap;
  }
  .firm-name .dot {
    width: 22px; height: 22px; border-radius: 50%;
    background: var(--red);
    align-self: center;
  }
  .firm-name .suffix {
    font-size: 9px; line-height: 18px; letter-spacing: 1px;
  }
  .firm-tagline {
    margin: 3px 0 0 32px;
    color: var(--red);
    font-weight: 700; font-size: 11px; letter-spacing: 5px;
    white-space: nowrap;
  }
  .portrait {
    position: absolute; left: 406px; top: 6px;
    width: 207px; height: 246px;
    background: linear-gradient(to bottom, var(--hair) 0%, #3a2c28 40%, var(--suit) 70%);
    border-radius: 90px 90px 0 0;
  }
  .headline {
    position: absolute; left: 661px; top: 37px;
    font-weight: 900; font-size: 100px; line-height: 96px;
    letter-spacing: -1px; white-space: nowrap;
  }
  .headline .line-one { display: block; color: var(--red); }
  .headline .line-two { display: block; color: var(--navy); }
  .contact-band {
    position: absolute; left: 0; bottom: 0;
    width: 1120px; height: 75px;
  }
  .contact-band svg { position: absolute; inset: 0; }
  .phone {
    position: absolute; left: 58px; top: 5px;
    color: var(--white);
    font-weight: 900; font-size: 58px; line-height: 66px;
    letter-spacing: 1px; white-space: nowrap;
  }
  .website {
    position: absolute; left: 770px; top: 27px; width: 330px;
    text-align: center;
    color: var(--white);
    font-size: 15px; letter-spacing: 3px;
    white-space: nowrap;
  }
  .website b { font-weight: 900; }
</style>
</head>
<body>
  <div class="billboard">
    <div class="emoji-art" role="img" aria-label="Personal injury settlement illustration: cartoon cash bundle with an open hand and a hand holding car keys"></div>
    <div class="firm">
      <div class="firm-name"><span class="dot"></span>HALDEN LAW FIRM <span class="suffix">PLLC</span></div>
      <div class="firm-tagline">AUNTIE VERDICT</div>
    </div>
    <div class="portrait" role="img" aria-label="Portrait photo of personal injury attorney Dottie in a black suit"></div>
    <h1 class="headline">
      <span class="line-one">AUNTIE</span>
      <span class="line-two">VERDICT</span>
    </h1>
    <div class="contact-band">
      <svg width="1120" height="75" viewBox="0 0 1120 75" aria-hidden="true">
        <polygon points="0,0 755,0 730,75 0,75" fill="var(--red)"/>
        <polygon points="770,0 1120,0 1120,75 745,75" fill="var(--navy)"/>
      </svg>
      <div class="phone">CALL: 555-417-9038</div>
      <div class="website">WWW.<b>AUNTIEVERDICT</b>.COM</div>
    </div>
  </div>
</body>
</html>
```